Online interactive calendar for training organisation

We have a new website being made and need a design for an online calendar that is interactive and very simple and easy to use. On our main page this calendar will include all of our courses (approx 30 different ones with up to 8 different locations). On our sub pages which have course information, the calendar will only include details of that specific course. Details needed are: Course code, course name/title, date, duration (1/2 day - 5 days), location, price, discount price. Maybe also a key for available or limited spots left? We want a section at the top of the calendar to be able to filter by location or course, and maybe to filter by month also? I have included a spreadsheet with a sample of our courses with this information. Also a sample draft of the main page on our new webpage to show the colour green which is our company colour. Main notes - we want as simple, effective and easy to use as possible.
We will need to know what plug in we can use to get the design you have created.

Target Market(s)

Mining and construction - both companies and individuals

Number of Pages Required

1 page

Colors
cadf82

Requirements
Must have
• Be simple, easy to use, effective.

```html
<!DOCTYPE html>
<html lang="en">
<head>
<meta charset="utf-8">
<title>Groundline Safety – Course Calendar</title>
<link href="https://fonts.googleapis.com/css2?family=Montserrat:wght@400;500;600;700;800&family=Roboto:wght@400;500&family=Roboto+Condensed:wght@400;700&display=swap" rel="stylesheet">
<style>
:root{
  --backdrop:#4a4a4a;
  --board:#f4f4f4;
  --white:#ffffff;
  --brand-green:#8cc63f;
  --accent-red:#c1000f;
  --accent-yellow:#e2d237;
  --ink:#1b1b1b;
  --muted:#6d6d6d;
  --navy:#1f2f8c;
  --line:#a9a9a9;
  --footer:#222222;
  --section-grey:#efefef;
}
*{box-sizing:border-box;margin:0;padding:0}
html,body{width:1200px;height:2198px;overflow:hidden}
body{background:var(--backdrop);font-family:"Montserrat",sans-serif;color:var(--ink);position:relative}

/* ---------- calendar component ---------- */
.cal-board{position:relative;width:1082px;height:589px;background:var(--board);overflow:hidden}
.cal-board__shapes{position:absolute;inset:0}
.cal-card{position:absolute;left:65px;top:78px;width:952px;height:434px;background:var(--white);box-shadow:0 2px 6px rgba(0,0,0,.12)}
.cal-card__title{position:absolute;top:30px;left:0;right:0;text-align:center;font-size:37px;font-weight:700;letter-spacing:.5px}
.cal-card__subtitle{position:absolute;top:84px;left:0;right:0;text-align:center;font-family:"Roboto",sans-serif;font-size:14px;color:var(--muted)}
.filters{position:absolute;top:144px;left:64px;display:flex;gap:20px}
.filter{width:262px;height:47px;border:1px solid var(--line);display:flex;align-items:center;justify-content:space-between;padding:0 18px}
.filter__label{font-size:11.5px;color:#555;line-height:1.35}
.filter__label sup,.req{color:var(--accent-red);font-size:9px}
.filter__value{display:block;font-weight:600;font-size:11.5px;color:var(--ink)}
.course-list{position:absolute;top:225px;left:66px;display:flex;gap:9px}
.course{position:relative;width:199px;height:144px;background:var(--white);border:1px solid #ececec;box-shadow:0 1px 4px rgba(0,0,0,.1);padding:46px 10px 0 14px}
.course__tag{position:absolute;left:0;top:0;width:82px;height:26px;background:var(--brand-green);color:var(--white);font-weight:700;font-size:12.5px;line-height:26px;padding-left:11px;clip-path:polygon(0 0,100% 0,88% 100%,0 100%)}
.course__meta{position:absolute;left:88px;top:9px;display:flex;gap:10px;font-size:11px;font-weight:700;align-items:center}
.course__meta span{display:flex;align-items:center;gap:4px}
.course__name{font-size:11.5px;font-weight:500;color:#707070;line-height:1.4}
.course__date{font-size:9.5px;color:#333;margin-top:6px}
.course__price{font-size:13px;font-weight:700;margin-top:6px}
.course__price b{color:var(--navy)}
.course__discount{font-size:12px;color:#333;margin-top:5px}
.course__discount b{color:var(--accent-red)}
.cal-card__note{position:absolute;left:64px;top:382px;font-size:11.5px;color:var(--accent-red)}

/* ---------- presentation placement ---------- */
.showcase-calendar{position:absolute;left:59px;top:82px}
.site{position:absolute;left:183px;top:710px;width:840px;height:1407px;background:var(--white);overflow:hidden}

/* ---------- site page ---------- */
.topbar{height:22px;background:var(--brand-green);position:relative}
.topbar__social{position:absolute;left:158px;top:5px;display:flex;gap:4px}
.topbar__social i{width:12px;height:12px;border-radius:50%;background:#1b1b1b;display:block}
.topbar__access{position:absolute;left:545px;top:4px;width:59px;height:14px;background:#1b1b1b;color:#fff;font-size:6px;font-weight:700;text-align:center;line-height:14px}
.topbar__search{position:absolute;left:608px;top:4px;width:74px;height:14px;background:#fff;border-radius:2px}
.topbar__search svg{position:absolute;right:6px;top:3px}
.header{height:49px;position:relative;border-bottom:1px solid #eee}
.brand{position:absolute;left:159px;top:12px;display:flex;align-items:center;gap:6px}
.brand__dot{width:28px;height:28px;border-radius:50%;background:var(--accent-red)}
.brand__name{font-weight:800;font-size:14px;color:var(--accent-red);line-height:1}
.brand__tag{display:block;font-size:6px;font-weight:600;color:#333;margin-top:3px;letter-spacing:.4px}
.nav{position:absolute;left:432px;top:21px;display:flex;gap:12px;font-family:"Roboto",sans-serif;font-size:6px;color:#333}
.nav a{color:inherit;text-decoration:none}
.nav .is-active{color:var(--brand-green)}
.difference{height:376px;background:var(--section-grey);position:relative}
.difference__title{position:absolute;top:30px;left:0;right:0;text-align:center;font-family:"Roboto Condensed",sans-serif;font-size:22px;color:#111}
.difference__sub{position:absolute;top:58px;left:0;right:0;text-align:center;font-family:"Roboto",sans-serif;font-size:7.5px;color:#222}
.difference__rule{position:absolute;top:78px;left:405px;width:34px;height:2px;background:var(--brand-green)}
.tiles{position:absolute;left:158px;top:101px;display:grid;grid-template-columns:repeat(5,96px);column-gap:11.7px;row-gap:33px}
.tile__img{width:96px;height:95px}
.tile__label{font-family:"Roboto",sans-serif;font-size:7.5px;text-align:center;margin-top:10px;color:#222}
.site-calendar{position:absolute;left:36px;top:500px;width:768px;height:418px}
.site-calendar .cal-board{transform:scale(.71);transform-origin:0 0}
.hero{position:absolute;left:0;top:969px;width:840px;height:283px;background:linear-gradient(100deg,#8a7a55 0%,#b3a06a 35%,#c8c4b8 60%,#dcdcd8 100%)}
.hero__frame{position:absolute;left:534px;top:46px;width:170px;height:192px;border:8px solid var(--white)}
.hero__title{position:absolute;left:455px;top:108px;font-family:"Roboto Condensed",sans-serif;font-weight:700;font-size:28px;line-height:1.05;color:#1d1d1d}
.hero__strip{position:absolute;left:455px;top:178px;width:229px;height:15px;background:var(--brand-green);color:#fff;font-family:"Roboto",sans-serif;font-size:6.3px;line-height:15px;text-align:center}
.footer{position:absolute;left:0;top:1251px;width:840px;height:128px;background:var(--footer)}
.footer .brand{top:38px}
.footer__follow{position:absolute;left:188px;top:78px;display:flex;align-items:center;gap:3px;font-family:"Roboto",sans-serif;font-size:7px;color:#ddd}
.footer__follow i{width:12px;height:12px;background:#fff;display:block;margin-left:2px}
.footer .nav{top:50px;color:#ddd}
.footer__contact{position:absolute;left:413px;top:74px;display:flex;gap:16px;font-family:"Roboto",sans-serif;font-size:6.5px;color:#ddd;align-items:center}
.footer__contact span{display:flex;align-items:center;gap:8px}
.footer__icon{width:14px;height:14px;background:#000;display:flex;align-items:center;justify-content:center}
.to-top{position:absolute;left:705px;top:108px;width:26px;height:26px;background:#fff;display:flex;align-items:center;justify-content:center;box-shadow:0 1px 3px rgba(0,0,0,.3)}
.copyright{position:absolute;left:0;top:1379px;width:840px;height:28px;background:var(--brand-green);font-family:"Roboto",sans-serif;font-size:6px;color:#222;text-align:center;line-height:28px}
</style>
</head>
<body>

<!-- Calendar presented on its own -->
<section class="showcase-calendar">
  <div class="cal-board">
    <svg class="cal-board__shapes" width="1082" height="589" aria-hidden="true">
      <circle cx="26" cy="72" r="160" fill="var(--accent-red)"/>
      <circle cx="1008" cy="545" r="183" fill="var(--accent-yellow)"/>
    </svg>
    <div class="cal-card">
      <h1 class="cal-card__title">CALENDAR</h1>
      <p class="cal-card__subtitle">Sed ut perspiciatis unde omnis iste natus</p>
      <div class="filters">
        <div class="filter"><span class="filter__label">Location <sup>*</sup><span class="filter__value">Cairns</span></span><svg width="12" height="8" viewBox="0 0 12 8"><path d="M1 1l5 5 5-5" fill="none" stroke="#222" stroke-width="1.6"/></svg></div>
        <div class="filter"><span class="filter__label">Course <sup>*</sup></span><svg width="12" height="8" viewBox="0 0 12 8"><path d="M1 1l5 5 5-5" fill="none" stroke="#222" stroke-width="1.6"/></svg></div>
        <div class="filter"><span class="filter__label">Month <sup>*</sup></span><svg width="12" height="8" viewBox="0 0 12 8"><path d="M1 1l5 5 5-5" fill="none" stroke="#222" stroke-width="1.6"/></svg></div>
      </div>
      <div class="course-list">
        <article class="course">
          <span class="course__tag">CAIRNS</span>
          <div class="course__meta"><span><svg width="9" height="9"><circle cx="4.5" cy="4.5" r="3.6" fill="none" stroke="var(--brand-green)" stroke-width="1.2"/><path d="M4.5 2.5v2h1.6" fill="none" stroke="var(--brand-green)" stroke-width="1"/></svg>7am</span><span><svg width="9" height="9"><rect x=".8" y="1.5" width="7.4" height="6.8" fill="none" stroke="var(--brand-green)" stroke-width="1.1"/><path d="M.8 3.6h7.4" stroke="var(--brand-green)"/></svg>1 day</span></div>
          <p class="course__name">S123 Supervisors <span class="req">*</span></p>
          <p class="course__date">Tuesday, December 10,2019</p>
          <p class="course__price">PRICE: <b>$ 450.00</b></p>
          <p class="course__discount">ISF discount price : <b>$ 100.00</b></p>
        </article>
        <article class="course">
          <span class="course__tag">CAIRNS</span>
          <div class="course__meta"><span><svg width="9" height="9"><circle cx="4.5" cy="4.5" r="3.6" fill="none" stroke="var(--brand-green)" stroke-width="1.2"/><path d="M4.5 2.5v2h1.6" fill="none" stroke="var(--brand-green)" stroke-width="1"/></svg>7am</span><span><svg width="9" height="9"><rect x=".8" y="1.5" width="7.4" height="6.8" fill="none" stroke="var(--brand-green)" stroke-width="1.1"/><path d="M.8 3.6h7.4" stroke="var(--brand-green)"/></svg>½ Day</span></div>
          <p class="course__name">RIIVEH201D – Light Vehicle</p>
          <p class="course__date">5th, 19th</p>
          <p class="course__price">PRICE: <b>$ 150.00</b></p>
          <p class="course__discount">ISF discount price : <b>$ 80.00</b></p>
        </article>
        <article class="course">
          <span class="course__tag">CAIRNS</span>
          <div class="course__meta"><span><svg width="9" height="9"><circle cx="4.5" cy="4.5" r="3.6" fill="none" stroke="var(--brand-green)" stroke-width="1.2"/><path d="M4.5 2.5v2h1.6" fill="none" stroke="var(--brand-green)" stroke-width="1"/></svg>8am</span><span><svg width="9" height="9"><rect x=".8" y="1.5" width="7.4" height="6.8" fill="none" stroke="var(--brand-green)" stroke-width="1.1"/><path d="M.8 3.6h7.4" stroke="var(--brand-green)"/></svg>5 days</span></div>
          <p class="course__name">CPCCCM205E Gantry crane</p>
          <p class="course__date">Tuesday, January 07, 2020</p>
          <p class="course__price">PRICE: <b>$ 1,250.00</b></p>
          <p class="course__discount">ISF discount price : <b>$ 650.00</b></p>
        </article>
        <article class="course">
          <span class="course__tag">CAIRNS</span>
          <div class="course__meta"><span><svg width="9" height="9"><circle cx="4.5" cy="4.5" r="3.6" fill="none" stroke="var(--brand-green)" stroke-width="1.2"/><path d="M4.5 2.5v2h1.6" fill="none" stroke="var(--brand-green)" stroke-width="1"/></svg>1pm</span><span><svg width="9" height="9"><rect x=".8" y="1.5" width="7.4" height="6.8" fill="none" stroke="var(--brand-green)" stroke-width="1.1"/><path d="M.8 3.6h7.4" stroke="var(--brand-green)"/></svg>1/2 day</span></div>
          <p class="course__name">RIIHAN304D Work safely at heights - practical only</p>
          <p class="course__date">Thursday, January 16, 2020</p>
          <p class="course__price">PRICE: <b>$ 80.00</b></p>
          <p class="course__discount">ISF discount price : <b>$ 00.00</b></p>
        </article>
      </div>
      <p class="cal-card__note">* Limited Spots left</p>
    </div>
  </div>
</section>

<!-- Home page -->
<main class="site">
  <div class="topbar">
    <div class="topbar__social"><i></i><i></i><i></i><i></i></div>
    <span class="topbar__access">Student Access</span>
    <span class="topbar__search"><svg width="7" height="7" viewBox="0 0 7 7"><circle cx="3" cy="3" r="2.2" fill="none" stroke="#222"/><path d="M4.6 4.6L6.6 6.6" stroke="#222"/></svg></span>
  </div>
  <header class="header">
    <div class="brand"><span class="brand__dot"></span><span><span class="brand__name">GROUNDLINE SAFETY</span><span class="brand__tag">SAFETY AND TRAINING</span></span></div>
    <nav class="nav"><a class="is-active">Home</a><a>Courses</a><a>Our Services</a><a>About us</a><a>Funding</a><a>Locations</a><a>Contact us</a></nav>
  </header>

  <section class="difference">
    <h2 class="difference__title">THE GROUNDLINE DIFFERENCE</h2>
    <p class="difference__sub">Committed to helping our students succeed.</p>
    <span class="difference__rule"></span>
    <div class="tiles">
      <div class="tile"><div class="tile__img" role="img" aria-label="Loader working in a quarry" style="background:linear-gradient(135deg,#6b6f72,#a39b86)"></div><p class="tile__label">All Courses</p></div>
      <div class="tile"><div class="tile__img" role="img" aria-label="Handshake with work gloves" style="background:linear-gradient(135deg,#5a9ee0,#b7d4ef)"></div><p class="tile__label">Funded courses</p></div>
      <div class="tile"><div class="tile__img" role="img" aria-label="Red tipper truck at a mine" style="background:linear-gradient(135deg,#8d8d8a,#b55b55)"></div><p class="tile__label">Mining</p></div>
      <div class="tile"><div class="tile__img" role="img" aria-label="Excavator on a rock face" style="background:linear-gradient(135deg,#bfc5cb,#4a4a44)"></div><p class="tile__label">Standard 11</p></div>
      <div class="tile"><div class="tile__img" role="img" aria-label="Workers on a roof at height" style="background:linear-gradient(135deg,#c9d7e2,#55616b)"></div><p class="tile__label">Work safely at heights</p></div>
      <div class="tile"><div class="tile__img" role="img" aria-label="Office team at a laptop" style="background:linear-gradient(135deg,#3c4d5f,#c4b8a8)"></div><p class="tile__label">Corporate clients</p></div>
      <div class="tile"><div class="tile__img" role="img" aria-label="Students studying online" style="background:linear-gradient(135deg,#d9a15a,#5b8fb9)"></div><p class="tile__label">Online courses</p></div>
      <div class="tile"><div class="tile__img" role="img" aria-label="Engineers reviewing plans on site" style="background:linear-gradient(135deg,#7fb0d8,#d8c34a)"></div><p class="tile__label">RPL's &amp; VOC's</p></div>
      <div class="tile"><div class="tile__img" role="img" aria-label="Operator in an elevated work platform" style="background:linear-gradient(135deg,#8aa0b5,#e0cf3a)"></div><p class="tile__label">Plant &amp; Equipment</p></div>
      <div class="tile"><div class="tile__img" role="img" aria-label="Construction worker on site" style="background:linear-gradient(135deg,#b96a2a,#3c3c3c)"></div><p class="tile__label">Construction</p></div>
    </div>
  </section>

  <div class="site-calendar">
    <div class="cal-board">
      <svg class="cal-board__shapes" width="1082" height="589" aria-hidden="true">
        <circle cx="26" cy="72" r="160" fill="var(--accent-red)"/>
        <circle cx="1008" cy="545" r="183" fill="var(--accent-yellow)"/>
      </svg>
      <div class="cal-card">
        <h2 class="cal-card__title">CALENDAR</h2>
        <p class="cal-card__subtitle">Sed ut perspiciatis unde omnis iste natus</p>
        <div class="filters">
          <div class="filter"><span class="filter__label">Location <sup>*</sup><span class="filter__value">Cairns</span></span><svg width="12" height="8" viewBox="0 0 12 8"><path d="M1 1l5 5 5-5" fill="none" stroke="#222" stroke-width="1.6"/></svg></div>
          <div class="filter"><span class="filter__label">Course <sup>*</sup></span><svg width="12" height="8" viewBox="0 0 12 8"><path d="M1 1l5 5 5-5" fill="none" stroke="#222" stroke-width="1.6"/></svg></div>
          <div class="filter"><span class="filter__label">Month <sup>*</sup></span><svg width="12" height="8" viewBox="0 0 12 8"><path d="M1 1l5 5 5-5" fill="none" stroke="#222" stroke-width="1.6"/></svg></div>
        </div>
        <div class="course-list">
          <article class="course">
            <span class="course__tag">CAIRNS</span>
            <div class="course__meta"><span><svg width="9" height="9"><circle cx="4.5" cy="4.5" r="3.6" fill="none" stroke="var(--brand-green)" stroke-width="1.2"/></svg>7am</span><span><svg width="9" height="9"><rect x=".8" y="1.5" width="7.4" height="6.8" fill="none" stroke="var(--brand-green)" stroke-width="1.1"/></svg>1 day</span></div>
            <p class="course__name">S123 Supervisors <span class="req">*</span></p>
            <p class="course__date">Tuesday, December 10,2019</p>
            <p class="course__price">PRICE: <b>$ 450.00</b></p>
            <p class="course__discount">ISF discount price : <b>$ 100.00</b></p>
          </article>
          <article class="course">
            <span class="course__tag">CAIRNS</span>
            <div class="course__meta"><span><svg width="9" height="9"><circle cx="4.5" cy="4.5" r="3.6" fill="none" stroke="var(--brand-green)" stroke-width="1.2"/></svg>7am</span><span><svg width="9" height="9"><rect x=".8" y="1.5" width="7.4" height="6.8" fill="none" stroke="var(--brand-green)" stroke-width="1.1"/></svg>½ Day</span></div>
            <p class="course__name">RIIVEH201D – Light Vehicle</p>
            <p class="course__date">5th, 19th</p>
            <p class="course__price">PRICE: <b>$ 150.00</b></p>
            <p class="course__discount">ISF discount price : <b>$ 80.00</b></p>
          </article>
          <article class="course">
            <span class="course__tag">CAIRNS</span>
            <div class="course__meta"><span><svg width="9" height="9"><circle cx="4.5" cy="4.5" r="3.6" fill="none" stroke="var(--brand-green)" stroke-width="1.2"/></svg>8am</span><span><svg width="9" height="9"><rect x=".8" y="1.5" width="7.4" height="6.8" fill="none" stroke="var(--brand-green)" stroke-width="1.1"/></svg>5 days</span></div>
            <p class="course__name">CPCCCM205E Gantry crane</p>
            <p class="course__date">Tuesday, January 07, 2020</p>
            <p class="course__price">PRICE: <b>$ 1,250.00</b></p>
            <p class="course__discount">ISF discount price : <b>$ 650.00</b></p>
          </article>
          <article class="course">
            <span class="course__tag">CAIRNS</span>
            <div class="course__meta"><span><svg width="9" height="9"><circle cx="4.5" cy="4.5" r="3.6" fill="none" stroke="var(--brand-green)" stroke-width="1.2"/></svg>1pm</span><span><svg width="9" height="9"><rect x=".8" y="1.5" width="7.4" height="6.8" fill="none" stroke="var(--brand-green)" stroke-width="1.1"/></svg>1/2 day</span></div>
            <p class="course__name">RIIHAN304D Work safely at heights - practical only</p>
            <p class="course__date">Thursday, January 16, 2020</p>
            <p class="course__price">PRICE: <b>$ 80.00</b></p>
            <p class="course__discount">ISF discount price : <b>$ 00.00</b></p>
          </article>
        </div>
        <p class="cal-card__note">* Limited Spots left</p>
      </div>
    </div>
  </div>

  <section class="hero" role="img" aria-label="Large yellow mining haul truck in an open-cut mine">
    <span class="hero__frame"></span>
    <h2 class="hero__title">Training a Safety<br>Culture that Counts</h2>
    <p class="hero__strip">NOW TRAINING - Working at Heights &amp; Confined Spaces courses</p>
  </section>

  <footer class="footer">
    <div class="brand"><span class="brand__dot"></span><span class="brand__name">GROUNDLINE SAFETY</span></div>
    <div class="footer__follow">Follow us on :- <i></i><i></i><i></i><i></i></div>
    <nav class="nav"><a>Home</a><a>Courses</a><a>Our Services</a><a>About us</a><a>Funding</a><a>Locations</a><a>Contact us</a></nav>
    <div class="footer__contact">
      <span><span class="footer__icon"><svg width="6" height="8" viewBox="0 0 6 8"><path d="M3 8C1 5 0 4 0 3a3 3 0 0 1 6 0c0 1-1 2-3 5z" fill="#fff"/><circle cx="3" cy="3" r="1" fill="#000"/></svg></span>18 Ridgeway Drive, Stonebridge QLD 4300</span>
      <span><span class="footer__icon"><svg width="8" height="6" viewBox="0 0 8 6"><rect width="8" height="6" fill="#fff"/><path d="M0 0l4 3 4-3" fill="none" stroke="#000" stroke-width=".8"/></svg></span>office@groundlinesafety.edu.au</span>
    </div>
    <span class="to-top"><svg width="10" height="6" viewBox="0 0 10 6"><path d="M1 5l4-4 4 4" fill="none" stroke="#222" stroke-width="1.4"/></svg></span>
  </footer>
  <p class="copyright">© Copyright All Right Reserved | Powered by Groundline Safety.</p>
</main>

</body>
</html>
```